Travel Agency Website - Simple General

Need a 7 page simple design that is pretty repetitive. Need to be able to load quickly that is SEO optimized. Trying to give ideas on what they can do, be personal as we are local, but at the same time come across as professional and get information easily with little burden.

- Landing Page
- Brimwell Vacations Page
- Family Trips
- Road Trips from Texas
- Other Destinations
- About Us Page
- Contact Us Page

Target Market(s)

Families

Coding

Coded - Design and coding required

Number of Pages Required

5+ page

Colors

Designer to choose colors to be used in the design.

Requirements
Must have
• Like it to flow easily with our logo. Use that for colors, etc.

```html
<!DOCTYPE html>
<html lang="en">
<head>
<meta charset="utf-8">
<title>Roam &amp; Ramble Travel Co. — Plan Your Perfect Trip</title>
<link rel="stylesheet" href="https://fonts.googleapis.com/css2?family=Outfit:wght@300;400;500;600;700;800&family=Fredoka:wght@500;600&display=swap">
<style>
:root{
  --teal:#1d5c64;
  --teal-soft:rgba(31,96,104,.9);
  --gold:#c9a15a;
  --gold-soft:rgba(201,160,88,.94);
  --cream:#f2f1ea;
  --mist:#e4e8e2;
  --white:#ffffff;
  --ph-blue-a:#9fb9cc;--ph-blue-b:#8aa8bd;
  --ph-slate-a:#b3c0c6;--ph-slate-b:#a1b0b7;
  --ph-sand-a:#c9b9a4;--ph-sand-b:#b9a892;
  --ph-rose-a:#c9b3ad;--ph-rose-b:#b9a39d;
}
*{margin:0;padding:0;box-sizing:border-box}
html,body{width:1200px;height:849px;overflow:hidden}
body{
  font-family:"Outfit",sans-serif;color:var(--teal);
  background:linear-gradient(180deg,#eef0eb 0%,var(--mist) 35%,var(--cream) 70%,var(--cream) 100%);
  position:relative;
}
.contact-bar{
  position:absolute;left:546px;top:0;width:584px;height:45px;
  background:var(--teal);border-radius:0 0 12px 12px;
  display:flex;align-items:center;gap:26px;padding-left:22px;color:var(--white);font-size:14px;
}
.contact-bar .item{display:flex;align-items:center;gap:9px}
.contact-bar .phone{font-size:15px;font-weight:500}
.contact-bar .icon{width:28px;height:28px;border-radius:50%;background:var(--white);display:flex;align-items:center;justify-content:center}
.brand{
  position:absolute;left:62px;top:40px;display:flex;align-items:center;gap:10px;
  font-weight:600;font-size:26px;color:var(--teal);
}
.brand .dot{width:26px;height:26px;border-radius:50%;background:var(--gold)}
.main-nav{position:absolute;left:305px;top:68px;height:40px;display:flex;align-items:center;font-size:16px}
.main-nav a{color:var(--teal);text-decoration:none;margin-right:23px}
.main-nav .home{margin-right:24px;display:flex}
.main-nav .about{margin-left:13px;margin-right:17px}
.cta{
  display:flex;align-items:center;gap:14px;background:var(--gold);color:var(--white);
  height:39px;padding:0 6px 0 27px;border-radius:20px;font-size:15px;
}
.main-nav a.cta{color:var(--white)}
.cta .arrow{width:28px;height:28px;border-radius:50%;background:#d9b36c;display:flex;align-items:center;justify-content:center}
.hero-kicker{position:absolute;top:168px;width:100%;text-align:center;font-size:31px;font-weight:300;letter-spacing:1px}
.hero-title{position:absolute;top:208px;width:100%;text-align:center;font-size:62px;font-weight:700;letter-spacing:1px}
.cards{position:absolute;top:323px;left:0;width:100%;height:370px}
.card{position:absolute;top:0;height:370px;width:267px;border-radius:6px;overflow:hidden}
.card .photo{position:absolute;inset:0}
.card .band{position:absolute;left:0;bottom:0;width:100%;height:92px}
.card .label{
  position:absolute;left:0;bottom:0;width:100%;height:64px;display:flex;flex-direction:column;
  align-items:center;justify-content:center;color:var(--white);font-family:"Fredoka",sans-serif;
  font-weight:600;font-size:17px;line-height:1.2;text-align:center;letter-spacing:.3px;
}
.card .label small{font-size:10.5px;font-weight:500;margin-top:3px;letter-spacing:.2px}
.c1{left:55px}.c2{left:331px}.c3{left:611px}.c4{left:886px}
.c1 .photo{background:linear-gradient(180deg,var(--ph-blue-a),var(--ph-blue-b))}
.c2 .photo{background:linear-gradient(180deg,var(--ph-slate-a),var(--ph-slate-b))}
.c3 .photo{background:linear-gradient(180deg,var(--ph-sand-a),var(--ph-sand-b))}
.c4 .photo{background:linear-gradient(180deg,var(--ph-rose-a),var(--ph-rose-b))}
.site-footer{position:absolute;left:0;top:783px;width:100%;height:66px;background:var(--white)}
.copyright{position:absolute;left:421px;top:26px;font-size:14px;font-weight:400;color:#2a3a3c;letter-spacing:.3px}
.social{position:absolute;left:1023px;top:16px;display:flex;gap:8px}
.social span{width:24px;height:24px;border-radius:50%;background:var(--teal)}
</style>
</head>
<body>
<header>
  <div class="contact-bar">
    <div class="item"><span class="icon"><svg width="14" height="11" viewBox="0 0 14 11"><rect x=".75" y=".75" width="12.5" height="9.5" rx="1.5" fill="none" stroke="#1d5c64" stroke-width="1.5"/><path d="M1 1.5 7 6l6-4.5" fill="none" stroke="#1d5c64" stroke-width="1.5"/></svg></span>RoamAndRamble@mailbox.com</div>
    <div class="item phone"><span class="icon"><svg width="14" height="14" viewBox="0 0 24 24"><path fill="#1d5c64" d="M6.6 10.8a15 15 0 0 0 6.6 6.6l2.2-2.2c.3-.3.7-.4 1-.2 1.1.4 2.3.6 3.6.6.6 0 1 .4 1 1V20c0 .6-.4 1-1 1A17 17 0 0 1 3 4c0-.6.4-1 1-1h3.5c.6 0 1 .4 1 1 0 1.2.2 2.4.6 3.6.1.3 0 .7-.2 1z"/></svg></span>Phone Number (555) 014 2368</div>
  </div>
  <div class="brand"><span class="dot"></span>Roam &amp; Ramble</div>
  <nav class="main-nav">
    <a class="home" href="#" aria-label="Home"><svg width="14" height="13" viewBox="0 0 14 13"><path fill="#c9a15a" d="M7 0 0 6h2v7h4V9h2v4h4V6h2z"/></svg></a>
    <a href="#">Brimwell Vacations</a>
    <a href="#">Family Trips</a>
    <a href="#">Texas Road Trips</a>
    <a href="#">Other Destinations</a>
    <a class="about" href="#">About Us</a>
    <a class="cta" href="#">Contact Us <span class="arrow"><svg width="10" height="10" viewBox="0 0 10 10"><path d="M2 8 8 2M3 2h5v5" fill="none" stroke="#fff" stroke-width="1.4"/></svg></span></a>
  </nav>
</header>

<main>
  <p class="hero-kicker">ROAM &amp; RAMBLE</p>
  <h1 class="hero-title">PLAN YOUR PERFECT TRIP</h1>

  <section class="cards">
    <article class="card c1">
      <div class="photo" role="img" aria-label="Photo: fairytale castle against a bright blue sky"></div>
      <svg class="band" viewBox="0 0 267 92" preserveAspectRatio="none"><path d="M0 22C60 22 100 22 120 10 140-2 150 0 170 12 190 22 230 22 267 22V92H0z" fill="var(--teal-soft)"/></svg>
      <div class="label">BRIMWELL VACATIONS<br>LAND &amp; SEA</div>
    </article>
    <article class="card c2">
      <div class="photo" role="img" aria-label="Photo: family hiking beside a mountain lake"></div>
      <svg class="band" viewBox="0 0 267 92" preserveAspectRatio="none"><path d="M0 22C60 22 100 22 120 10 140-2 150 0 170 12 190 22 230 22 267 22V92H0z" fill="var(--gold-soft)"/></svg>
      <div class="label">FAMILY TRIPS</div>
    </article>
    <article class="card c3">
      <div class="photo" role="img" aria-label="Photo: winding road through a red rock canyon"></div>
      <svg class="band" viewBox="0 0 267 92" preserveAspectRatio="none"><path d="M0 22C60 22 100 22 120 10 140-2 150 0 170 12 190 22 230 22 267 22V92H0z" fill="var(--teal-soft)"/></svg>
      <div class="label">TEXAS ROAD TRIPS<small>(Partnership with Piney Trail Van Rentals</small></div>
    </article>
    <article class="card c4">
      <div class="photo" role="img" aria-label="Photo: colourful cliffside seaside village"></div>
      <svg class="band" viewBox="0 0 267 92" preserveAspectRatio="none"><path d="M0 22C60 22 100 22 120 10 140-2 150 0 170 12 190 22 230 22 267 22V92H0z" fill="var(--teal-soft)"/></svg>
      <div class="label">OTHER DESTINATIONS</div>
    </article>
  </section>
</main>

<footer class="site-footer">
  <p class="copyright">© 2026 Roam &amp; Ramble. All Right Reserved</p>
  <div class="social"><span aria-label="Social profile one"></span><span aria-label="Social profile two"></span></div>
</footer>
</body>
</html>
```